Tattoo Care Kit

We need a retail box for a tattoo care product. The marketing name for this product is fennelquist.

Fennelquist will contain 2 tubes of product: 1) 4% lidocaine and 2) Vitamin A & D cream. Lidocaine will be used to numb the pain immediately after it is designed and the A & D post creation to protect the skin and ink.

Fennelquist is considered an OTC (Over-the-Counter) product/medication so we are looking for that pharma look. Nonetheless, we want to have a "tattoo" parlor element to it: skull, bones, tattoo, etc.

I have enclosed two graphics of the best sellers out there. The Box will be vertical like the brv7 graphic

We are open to foils, embossing, special varnishes and laminated board stock being used on the graphics. Fennelquist will be a very high end product.

```html
<!DOCTYPE html>
<html lang="en">
<head>
<meta charset="utf-8">
<title>Fennelquist Pack Proposal</title>
<link rel="stylesheet" href="https://fonts.googleapis.com/css2?family=Roboto+Condensed:wght@400;700&family=Montserrat:wght@300&display=swap">
<style>
  :root {
    --sheet: #ffffff;
    --fire-deep: #3a0a03;
    --fire-mid: #a8300c;
    --fire-hot: #e8781e;
    --fire-glow: #f6b040;
    --ink: #0b0807;
    --smoke: #1c1817;
    --bone: #8b8e96;
    --bone-shade: #3f3a36;
    --wordmark: #f2a24c;
    --copy-yellow: #f7e81c;
    --bullet-white: #f4f4f4;
    --bullet-blue: #8fcff0;
    --tube-dark: #141212;
    --rule: #a9c4d4;
    --caption: #7d8c96;
  }
  * { margin: 0; padding: 0; box-sizing: border-box; }
  html, body { width: 1200px; height: 849px; overflow: hidden; background: var(--sheet); }
  .sheet { position: relative; width: 1200px; height: 849px; background: var(--sheet); }

  .fire {
    background:
      radial-gradient(ellipse at 30% 60%, var(--fire-glow) 0%, transparent 35%),
      radial-gradient(ellipse at 75% 40%, var(--fire-hot) 0%, transparent 45%),
      linear-gradient(180deg, var(--fire-mid), var(--fire-deep) 55%, var(--fire-mid));
  }

  .wordmark {
    position: absolute;
    font-family: "Roboto Condensed", sans-serif;
    font-weight: 700;
    color: var(--wordmark);
    text-transform: uppercase;
    white-space: nowrap;
    line-height: 1;
  }

  .flap { position: absolute; left: 435px; width: 420px; height: 94px; overflow: hidden; }
  .flap--top { top: 57px; }
  .flap--bottom { top: 604px; }
  .flap .wordmark { left: 0; right: 0; text-align: center; top: 14px; font-size: 66px; letter-spacing: 1px; }
  .flap--top .wordmark { transform: rotate(180deg); }

  .front { position: absolute; left: 315px; top: 150px; width: 570px; height: 454px; overflow: hidden; }
  .front__fire { position: absolute; inset: 0; }

  .wordmark--down { writing-mode: vertical-rl; left: 10px; top: 14px; font-size: 76px; letter-spacing: 1px; }
  .wordmark--up { writing-mode: vertical-rl; transform: rotate(180deg); left: 110px; top: 14px; font-size: 76px; letter-spacing: 1px; }

  .skull {
    position: absolute; left: 190px; top: 110px; width: 230px; height: 344px;
    background: radial-gradient(ellipse at 45% 45%, var(--bone) 0%, var(--bone-shade) 60%, transparent 80%);
    opacity: .85;
  }

  .headband { position: absolute; left: 196px; top: 0; width: 374px; height: 220px; }

  .claims {
    position: absolute; left: 208px; top: 22px; list-style: none;
    font-family: "Roboto Condensed", sans-serif; font-weight: 700;
    font-size: 16.5px; line-height: 20px; color: var(--copy-yellow);
  }
  .claims li { position: relative; padding-left: 14px; margin-bottom: 1px; }
  .claims li::before {
    content: ""; position: absolute; left: 0; top: 6px; width: 9px; height: 9px; border-radius: 50%;
    background: var(--bullet-white);
  }
  .claims li.claims__item--cream::before { background: var(--bullet-blue); }
  .claims .indent { padding-left: 14px; display: block; }

  .tubes {
    position: absolute; left: 390px; top: 226px; width: 150px; height: 214px;
    background: linear-gradient(90deg, var(--tube-dark) 0 46%, transparent 46% 52%, var(--tube-dark) 52% 100%);
    border-radius: 6px 6px 0 0;
  }
  .tube-labels {
    position: absolute; left: 390px; top: 442px; width: 170px; display: flex; gap: 12px;
    font-family: "Roboto Condensed", sans-serif; font-weight: 700; font-size: 10.5px; color: var(--copy-yellow);
  }
  .tube-labels span:first-child { width: 58px; text-align: center; }

  .footer-rule { position: absolute; left: 0; top: 755px; width: 1200px; height: 4px; background: var(--rule); }
  .footer-caption {
    position: absolute; right: 10px; top: 784px;
    font-family: "Montserrat", sans-serif; font-weight: 300; font-size: 13px;
    letter-spacing: .48em; color: var(--caption); text-transform: uppercase;
  }
</style>
</head>
<body>
<main class="sheet">
  <section class="flap flap--top fire" role="img" aria-label="Flames background behind the product name, top flap">
    <span class="wordmark">Fennelquist</span>
  </section>

  <section class="front">
    <div class="front__fire fire" role="img" aria-label="Flames background"></div>
    <div class="skull" role="img" aria-label="Illustrated skull emerging from flames"></div>
    <svg class="headband" viewBox="0 0 374 220" aria-hidden="true">
      <defs>
        <linearGradient id="band-shade" x1="0" y1="0" x2="0" y2="1">
          <stop offset="0" stop-color="#0b0807" stop-opacity=".97"/>
          <stop offset="1" stop-color="#1c1817" stop-opacity=".85"/>
        </linearGradient>
      </defs>
      <path d="M0 0 H374 V180 C300 175 200 150 110 110 C60 88 20 60 0 40 Z" fill="url(#band-shade)"/>
    </svg>
    <span class="wordmark wordmark--down">Fennelquist</span>
    <span class="wordmark wordmark--up">Fennelquist</span>
    <ul class="claims">
      <li>4% Lidocaine - to be used to numb<span class="indent">the pain immediately after it is designed</span></li>
      <li class="claims__item--cream">Vitamin A &amp; D cream post creation<span class="indent">to protect the skin and ink.</span></li>
    </ul>
    <div class="tubes" role="img" aria-label="Two product tubes, lidocaine and vitamin A and D cream"></div>
    <div class="tube-labels"><span>Lidocaine</span><span>Vitamin A &amp; D</span></div>
  </section>

  <section class="flap flap--bottom fire" role="img" aria-label="Flames background behind the product name, bottom flap">
    <span class="wordmark">Fennelquist</span>
  </section>

  <div class="footer-rule"></div>
  <p class="footer-caption">Proposal for Fennelquist pack</p>
</main>
</body>
</html>
```